Business Card for beauty technology startup

Design Glimora Business Card for a Beauty, based on the website identity and colors (https://www.glimora-example.com).
Glimora is a beauty tech startup that gathers helpful product info for beauty lovers and consumers (such as availability on stores, price range and product reviews) for makeup products. The card design must be young, colorful but clean, and very modern.

Target Market(s)

woman, 15-35

Industry/Entity Type

Cosmetics

Contact Information for Business Card

Full Name, address, phone

Font styles to use
Other font styles liked:
• Advent Pro

Colors
e34297
86cfc6
ffffff
5c5c5c
e8e8e8
e667a6
b2b2b2

Requirements
Must have
• One full colored side with a creative design and another with card info
• Use Color palette: #95C5C5 and/or #D38AA5
• Use fonts: Advent Pro
• Use website identity: https://www.glimora-example.com
Nice to have
• If needed extra font: Roboto

```html
<!DOCTYPE html>
<html lang="en">
<head>
<meta charset="utf-8">
<title>Glimora Business Card</title>
<link rel="stylesheet" href="https://fonts.googleapis.com/css2?family=Advent+Pro:wght@300&family=Roboto+Condensed:wght@500&family=Roboto:wght@400&display=swap">
<style>
  :root {
    --page-bg: #e8e8e8;
    --card-front: #f6f6f6;
    --card-back: #18191b;
    --mauve: #b77d97;
    --mauve-faint: rgba(183, 125, 151, 0.12);
    --ink: #5c5c5c;
    --ink-dark: #444446;
    --rule: #b2b2b2;
    --white: #ffffff;
  }
  * { box-sizing: border-box; margin: 0; padding: 0; }
  html, body { width: 1200px; height: 960px; overflow: hidden; }
  body {
    position: relative;
    background: var(--page-bg);
    font-family: "Roboto", Arial, sans-serif;
  }
  .card {
    position: absolute;
    width: 600px;
    height: 343px;
    border-radius: 22px;
    overflow: hidden;
    box-shadow: 0 2px 6px rgba(0, 0, 0, 0.25);
  }
  .card-front { left: 314px; top: 113px; background: var(--card-front); }
  .card-back  { left: 311px; top: 472px; background: var(--card-back); }

  .front-ring {
    position: absolute;
    left: 112px; top: 18px;
    width: 300px; height: 300px;
    border: 3px solid var(--mauve-faint);
    border-radius: 50%;
  }
  .person {
    position: absolute;
    left: 34px; top: 33px;
    display: flex;
    align-items: center;
  }
  .person-name {
    font-family: "Roboto Condensed", "Arial Narrow", sans-serif;
    font-weight: 500;
    font-size: 21px;
    color: var(--mauve);
    letter-spacing: 0.2px;
  }
  .person-divider {
    width: 1px; height: 26px;
    background: var(--rule);
    margin: 0 6px 0 11px;
  }
  .person-role {
    font-size: 15px;
    color: var(--ink-dark);
  }
  .address {
    position: absolute;
    right: 35px; top: 183px;
    text-align: right;
    font-size: 15px;
    line-height: 19px;
    color: var(--ink);
  }
  .contacts {
    position: absolute;
    right: 36px; top: 230px;
    list-style: none;
  }
  .contacts li {
    display: flex;
    justify-content: flex-end;
    align-items: center;
    height: 19px;
    font-size: 15px;
    color: var(--ink-dark);
  }
  .contacts svg {
    width: 14px; height: 14px;
    margin-left: 14px;
    fill: var(--mauve);
  }

  .brand {
    position: absolute;
    left: 0; right: 0; top: 78px;
    display: flex;
    flex-direction: column;
    align-items: center;
  }
  .brand-dot {
    width: 96px; height: 96px;
    border: 3px solid var(--mauve);
    border-radius: 50%;
  }
  .brand-name {
    margin-top: 26px;
    font-family: "Advent Pro", "Roboto", sans-serif;
    font-weight: 300;
    font-size: 46px;
    letter-spacing: 6px;
    color: var(--mauve);
    line-height: 1;
  }
  .website {
    position: absolute;
    left: 0; right: 0; top: 294px;
    text-align: center;
    font-size: 14px;
    letter-spacing: 5px;
    color: var(--white);
  }
</style>
</head>
<body>
  <section class="card card-front" aria-label="Card front">
    <div class="front-ring"></div>
    <div class="person">
      <span class="person-name">MAREN HOLT</span>
      <span class="person-divider"></span>
      <span class="person-role">CEO/FOUNDER</span>
    </div>
    <address class="address" style="font-style:normal">
      2140 Lilac Court<br>Fairbanks, Alaska 34580
    </address>
    <ul class="contacts">
      <li>555 014 2231
        <svg viewBox="0 0 24 24" aria-hidden="true"><path d="M6.6 10.8a15 15 0 0 0 6.6 6.6l2.2-2.2c.3-.3.7-.4 1-.2 1.1.4 2.3.6 3.6.6.6 0 1 .4 1 1V20c0 .6-.4 1-1 1A17 17 0 0 1 3 4c0-.6.4-1 1-1h3.5c.6 0 1 .4 1 1 0 1.3.2 2.5.6 3.6.1.3 0 .7-.2 1z"/></svg>
      </li>
      <li>555 017 4482
        <svg viewBox="0 0 24 24" aria-hidden="true"><path d="M7 1h10a2 2 0 0 1 2 2v18a2 2 0 0 1-2 2H7a2 2 0 0 1-2-2V3a2 2 0 0 1 2-2zm0 3v14h10V4zm5 15.5a1 1 0 1 0 0 2 1 1 0 0 0 0-2z"/></svg>
      </li>
      <li>555 019 3307
        <svg viewBox="0 0 24 24" aria-hidden="true"><path d="M6 2h10l2 2v5H6zM3 10h18a2 2 0 0 1 2 2v7H1v-7a2 2 0 0 1 2-2zm3 6v6h12v-6z"/></svg>
      </li>
      <li>info@glimora-example.com
        <svg viewBox="0 0 24 24" aria-hidden="true"><path d="M2 5h20v14H2zm2 2v.5l8 5 8-5V7l-8 5z"/></svg>
      </li>
    </ul>
  </section>

  <section class="card card-back" aria-label="Card back">
    <div class="brand">
      <span class="brand-dot"></span>
      <span class="brand-name">GLIMORA</span>
    </div>
    <p class="website">www.glimora-example.com</p>
  </section>
</body>
</html>
```